Smile club flyer design

I am launching an office smile club and would like a design that sits my branding and that is appealing to customers. I have a design (I need a new one) that has all the information.
My website is maplehavendentalcarekx.com
Brand color is green. The design can be any color

Target Market(s)

Ages 30+

Industry/Entity Type

Dental

Font styles to use
Serif

Requirements
Must have
• Appealing to patients

```html
<!DOCTYPE html>
<html lang="en">
<head>
<meta charset="utf-8">
<title>Maplehaven Dental Care – Smile Club Membership</title>
<link rel="stylesheet" href="https://fonts.googleapis.com/css2?family=Anton&family=Allura&family=Crimson+Pro:wght@400;600&family=Roboto+Condensed:wght@400;700&family=Montserrat:ital,wght@0,700;1,600&display=swap">
<style>
:root{
  --green:#088c3c;
  --green-dark:#06732f;
  --mint:#b2fdd3;
  --card-bg:#eefdf4;
  --yellow:#ffe600;
  --ink:#0b0b0b;
  --white:#ffffff;
  --stage:#111111;
}
*{box-sizing:border-box;margin:0;padding:0}
html,body{width:924px;height:1200px;overflow:hidden;background:var(--stage)}
.flyer{position:absolute;left:62px;top:0;width:800px;height:1200px;background:var(--white);overflow:hidden;font-family:"Roboto Condensed",sans-serif}
.backdrop{position:absolute;inset:0}
.brand{position:absolute;left:100px;top:22px;width:336px;text-align:center;color:var(--green)}
.brand-name{font-family:"Crimson Pro",serif;font-weight:600;font-size:52px;line-height:1}
.brand-sub{font-family:"Montserrat",sans-serif;font-weight:700;font-size:17px;letter-spacing:6px;margin-top:2px}
.brand-sub::before,.brand-sub::after{content:"";display:inline-block;width:30px;height:2px;background:var(--green);vertical-align:middle;margin:0 8px}
.intro{position:absolute;left:150px;top:120px;font-family:"Allura",cursive;font-size:56px;color:var(--ink);line-height:1}
.title-club{position:absolute;left:82px;top:172px;width:340px;text-align:center;font-family:"Anton",sans-serif;font-size:78px;line-height:1;color:var(--green)}
.title-member{position:absolute;left:52px;top:258px;width:400px;text-align:center;font-family:"Anton",sans-serif;font-size:82px;line-height:1;color:var(--ink)}
.tagline{position:absolute;left:50px;top:364px;width:400px;text-align:center;font-weight:700;font-style:italic;font-size:17px;color:var(--ink)}
.hero{position:absolute;left:472px;top:56px;width:328px;height:440px}
.card{position:absolute;top:546px;width:219px;height:292px;background:var(--card-bg);box-shadow:0 2px 8px rgba(0,0,0,.25)}
.card-head{position:absolute;left:0;top:0}
.card-title{position:absolute;left:0;top:8px;width:100%;text-align:center;font-family:"Crimson Pro",serif;font-weight:600;font-size:23px;color:var(--yellow);line-height:1}
.card-sub{position:absolute;left:0;top:31px;width:100%;text-align:center;font-family:"Crimson Pro",serif;font-size:18px;color:var(--white);line-height:1}
.price{position:absolute;left:74px;top:58px;width:72px;height:72px;border-radius:50%;background:var(--green-dark);border:3px solid var(--white);color:var(--white);text-align:center;font-family:"Anton",sans-serif}
.price-amt{font-size:30px;line-height:1;margin-top:8px;display:block}
.price-per{font-size:11px;display:block}
.features{position:absolute;left:16px;top:152px;right:10px;list-style:none;font-size:12.2px;color:var(--ink);line-height:15px}
.features li{padding-left:20px;position:relative;margin-bottom:8.5px}
.features li::before{content:"";position:absolute;left:2px;top:4px;width:8px;height:6px;border-radius:0 6px 0 6px;background:var(--green)}
.card-core{left:46px}
.card-bright{left:291px}
.card-bright .card-head path{fill:var(--green-dark)}
.card-total{left:535px}
.card-refresh{left:56px;top:908px;height:228px}
.card-refresh .card-head path{fill:var(--green-dark)}
.card-refresh .features{top:158px}
.card-refresh .price{background:var(--green)}
.card-refresh .price-amt{margin-top:18px;font-size:28px}
.ribbon{position:absolute;left:-6px;top:0;width:58px;height:58px;overflow:hidden}
.ribbon span{position:absolute;left:-22px;top:14px;width:90px;transform:rotate(-45deg);background:var(--green);color:var(--white);font-family:"Crimson Pro",serif;font-size:12px;text-align:center;line-height:18px}
.finance{position:absolute;left:331px;top:893px;color:var(--white)}
.finance-head{font-family:"Montserrat",sans-serif;font-weight:700;font-size:16.5px;color:var(--yellow)}
.partners{display:flex;gap:32px;margin-top:12px;font-family:"Montserrat",sans-serif;font-weight:700;font-size:26px;color:var(--white);align-items:center}
.partners span::before{content:"";display:inline-block;width:16px;height:16px;border-radius:50%;background:var(--white);margin-right:8px;vertical-align:1px}
.plans{font-family:"Montserrat",sans-serif;font-weight:700;font-size:14px;letter-spacing:.5px;margin-top:10px}
.fee{font-family:"Montserrat",sans-serif;font-style:italic;font-weight:600;font-size:13.5px;margin-top:8px}
.cta{font-family:"Anton",sans-serif;font-size:46px;color:var(--yellow);line-height:1;margin-top:14px}
.phone{font-family:"Anton",sans-serif;font-size:50px;line-height:1;margin-top:14px}
</style>
</head>
<body>
<main class="flyer">
  <svg class="backdrop" width="800" height="1200" viewBox="0 0 800 1200" aria-hidden="true">
    <path d="M0,0 H646 V380 C560,440 470,520 300,530 C180,535 80,480 0,420 Z" fill="var(--mint)"/>
    <path d="M0,400 C90,460 180,510 300,530 C180,520 90,480 0,430 Z" fill="var(--green)"/>
    <path d="M0,880 C40,760 200,660 400,655 C600,660 720,770 760,880 C800,980 800,1100 780,1200 L0,1200 Z" fill="var(--mint)"/>
    <path d="M0,905 C40,770 200,682 400,676 C590,680 700,780 735,880 C770,980 760,1100 730,1200 L0,1200 Z" fill="var(--green)"/>
    <path d="M760,1000 L800,1060 V1200 H760 Z" fill="var(--mint)"/>
  </svg>

  <div class="brand">
    <div class="brand-name">Maplehaven</div>
    <div class="brand-sub">DENTAL CARE</div>
  </div>
  <div class="intro">Introducing</div>
  <h1 class="title-club">SMILE CLUB</h1>
  <div class="title-member">MEMBERSHIP</div>
  <p class="tagline">AFFORDABLE DENTAL CARE - NO INSURANCE REQUIRED</p>

  <svg class="hero" viewBox="0 0 328 440" role="img" aria-label="Photo of a dentist in mask and face shield treating a smiling female patient">
    <defs><linearGradient id="heroFill" x1="0" y1="0" x2="1" y2="1"><stop offset="0" stop-color="#dfe6ee"/><stop offset=".6" stop-color="#c9d2dc"/><stop offset="1" stop-color="#e8dcd4"/></linearGradient></defs>
    <path d="M150,8 Q178,-6 206,10 L328,90 V360 L206,430 Q178,446 150,430 L30,352 Q6,336 6,306 V134 Q6,104 30,88 Z" fill="var(--green)"/>
    <path d="M152,24 Q178,10 204,26 L328,106 V346 L204,416 Q178,430 152,414 L40,342 Q20,328 20,302 V138 Q20,112 40,98 Z" fill="url(#heroFill)"/>
  </svg>

  <article class="card card-core">
    <svg class="card-head" width="219" height="110" aria-hidden="true"><path d="M0,0 H219 V56 L110,112 L0,56 Z" fill="var(--green)"/></svg>
    <h2 class="card-title">CORE CARE</h2><div class="card-sub">Preventive</div>
    <div class="price"><span class="price-amt">$39</span><span class="price-per">/MONTH</span></div>
    <ul class="features"><li>Comprehensive Annual Exam</li><li>2 Professional Cleanings per Year</li><li>Routine Bitewing X-rays</li><li>10% Savings on Treatment</li></ul>
  </article>

  <article class="card card-bright">
    <svg class="card-head" width="219" height="110" aria-hidden="true"><path d="M0,0 H219 V56 L110,112 L0,56 Z"/></svg>
    <h2 class="card-title">BRIGHT</h2><div class="card-sub">Cosmetic</div>
    <div class="price"><span class="price-amt">$59</span><span class="price-per">/MONTH</span></div>
    <ul class="features"><li>Annual In-Office Whitening (Top &amp; Bottom)</li><li>Custom Whitening Trays</li><li>15% Savings on Elective Treatment</li></ul>
  </article>

  <article class="card card-total">
    <svg class="card-head" width="219" height="110" aria-hidden="true"><path d="M0,0 H219 V56 L110,112 L0,56 Z" fill="var(--green)"/></svg>
    <h2 class="card-title">TOTAL SMILE</h2><div class="card-sub">Periodontal</div>
    <div class="price"><span class="price-amt">$89</span><span class="price-per">/MONTH</span></div>
    <ul class="features"><li>3-4 Perio Maintenance Visits per Year</li><li>1 Comprehensive Exam</li><li>Diagnostic X-rays</li><li>15% Savings on Restorative &amp; Elective Care</li></ul>
  </article>

  <article class="card card-refresh">
    <svg class="card-head" width="219" height="110" aria-hidden="true"><path d="M0,0 H219 V56 L110,112 L0,56 Z"/></svg>
    <div class="ribbon"><span>NEW</span></div>
    <h2 class="card-title">SMILE</h2><div class="card-sub">Refresh Package</div>
    <div class="price"><span class="price-amt">$499</span></div>
    <ul class="features"><li>Cleaning + Comprehensive Exam + Whitening</li><li>Limited Time Offer</li></ul>
  </article>

  <section class="finance">
    <h3 class="finance-head">FLEXIBLE FINANCING FOR TREATMENTS</h3>
    <div class="partners"><span>KindPay</span><span>PlumFi</span></div>
    <p class="plans">PAYMENT PLANS AVAILABLE</p>
    <p class="fee">*$49 Lifetime Activation Fee (Non-refundable)</p>
    <p class="cta">JOIN SMILE CLUB TODAY!</p>
    <p class="phone">555-014-2290</p>
  </section>
</main>
</body>
</html>
```